Business card for Luxury Portable Restroom Trailer company

We are a Luxury Portable Restroom Trailer Company Called FALCRIDGE HIRES. Based in Orange County California. We provide portable restroom trailers for events, such as, Weddings, Concerts, Charity events, Sporting events, Tournaments, Corporate events, ect. We rent and Sell the Luxury restrooms. Our colors are white, grey, and Orange. As you will see in the logo we uploaded.
There are 2 people in the company so the names and titles will change for the 3 people but card will remain the same. Here is the information for each Person: Dwight Penner CFO 555 318-0476
next Person: Leon Marchetti VP 555 318-0476
Next Person: Owen Marchetti CEO 555 318-0476
Information to include on the card: Luxury Restroom Trailers Rental and Sales. Weddings, Concerts, Charity, Sporting and Corp. Events.

```html
<!DOCTYPE html>
<html lang="en">
<head>
<meta charset="utf-8">
<title>Falcridge Hires — Business Card</title>
<link href="https://fonts.googleapis.com/css2?family=Roboto:wght@400;500;700;900&display=swap" rel="stylesheet">
<style>
  :root{
    --page:#e9e9ea;
    --charcoal:#4a4a4c;
    --grey-text:#555558;
    --orange:#e8691f;
    --white:#ffffff;
    --paper:#fbfbfb;
  }
  *{box-sizing:border-box;margin:0;padding:0}
  html,body{width:1200px;height:960px;overflow:hidden}
  body{background:var(--page);font-family:"Roboto",Arial,sans-serif;position:relative}

  .card{position:absolute;left:220px;width:760px;height:434px;border-radius:22px;overflow:hidden;
        box-shadow:0 6px 18px rgba(0,0,0,.18)}
  .card--back{top:30px;background:var(--charcoal);color:var(--white)}
  .card--front{top:496px;background:var(--paper);color:var(--grey-text)}

  .wordmark{display:flex;align-items:center;gap:14px;font-weight:900;letter-spacing:1px;white-space:nowrap}
  .wordmark__square{width:26px;height:26px;flex:none}

  .card--back .wordmark{position:absolute;left:0;right:0;top:130px;justify-content:center;font-size:52px;color:var(--white)}
  .card--back .wordmark__square{background:var(--orange);width:34px;height:34px}
  .tagline{position:absolute;left:0;right:0;top:250px;text-align:center;font-size:19px;line-height:1.45;color:var(--white)}

  .card--front .wordmark{position:absolute;left:44px;top:190px;font-size:33px;color:var(--grey-text)}
  .card--front .wordmark__square{background:var(--orange)}

  .divider{position:absolute;left:438px;top:40px;width:1px;height:300px;background:#d6d6d6}

  .contact{position:absolute;left:468px;top:56px}
  .contact__name{font-size:30px;font-weight:700;color:var(--orange);letter-spacing:.5px}
  .contact__title{font-size:19px;color:#7a7a7d;margin-top:2px}
  .contact__address{font-size:18px;line-height:1.35;margin-top:22px;color:#333}
  .contact__list{list-style:none;margin-top:18px}
  .contact__item{display:flex;align-items:center;gap:12px;font-size:18px;line-height:1.55;color:#333}
  .contact__item svg{width:16px;height:16px;flex:none;fill:var(--orange)}

  .band-grey{position:absolute;left:0;right:0;bottom:0;height:16px;background:var(--charcoal)}
  .band-orange{position:absolute;right:0;bottom:0;width:260px;height:62px;background:var(--orange);
               clip-path:polygon(0 70%,0 100%,100% 100%,100% 0,12% 0,12% 70%)}
</style>
</head>
<body>
  <section class="card card--back" aria-label="Card back">
    <div class="wordmark"><span class="wordmark__square"></span><span>FALCRIDGE HIRES</span></div>
    <p class="tagline">Luxury Restroom Trailers Rental and Sales<br>Weddings, Concerts, Charity, Sporting and Corp Events</p>
  </section>

  <section class="card card--front" aria-label="Card front">
    <div class="wordmark"><span class="wordmark__square"></span><span>FALCRIDGE HIRES</span></div>
    <div class="divider"></div>
    <div class="contact">
      <h1 class="contact__name">DWIGHT PENNER</h1>
      <p class="contact__title">CFO</p>
      <p class="contact__address">2190 Harbor Crest Lane<br>Lakemont, CA 92710</p>
      <ul class="contact__list">
        <li class="contact__item">
          <svg viewBox="0 0 24 24" aria-hidden="true"><path d="M6.6 10.8a15.1 15.1 0 0 0 6.6 6.6l2.2-2.2a1 1 0 0 1 1-.25 11.4 11.4 0 0 0 3.6.57 1 1 0 0 1 1 1V20a1 1 0 0 1-1 1A17 17 0 0 1 3 4a1 1 0 0 1 1-1h3.5a1 1 0 0 1 1 1c0 1.25.2 2.45.57 3.57a1 1 0 0 1-.25 1z"/></svg>
          555 318-0476</li>
        <li class="contact__item">
          <svg viewBox="0 0 24 24" aria-hidden="true"><path d="M2 5h20v14H2zm2 2v.5l8 5 8-5V7l-8 5z"/></svg>
          name@falcridgehires.com</li>
        <li class="contact__item">
          <svg viewBox="0 0 24 24" aria-hidden="true"><circle cx="12" cy="12" r="10"/></svg>
          www.falcridgehires.com</li>
      </ul>
    </div>
    <div class="band-grey"></div>
    <div class="band-orange"></div>
  </section>
</body>
</html>
```